Copper Ridge Inquiries Letterhead

I would like to design a letterhead for a private investigation company. Our primary clients will be law firms. The business card is included below

```html
<!DOCTYPE html>
<html lang="en">
<head>
<meta charset="utf-8">
<title>Copper Ridge Inquiries Letterhead</title>
<link href="https://fonts.googleapis.com/css2?family=Montserrat:wght@400;500;700&display=swap" rel="stylesheet">
<style>
  :root {
    --backdrop: #e4e4e6;
    --paper: #ffffff;
    --navy: #1d2f5c;
    --copper: #f05a2b;
    --ink: #2a2a2a;
    --faint: #f3f2f4;
  }
  html, body {
    margin: 0;
    padding: 0;
    width: 1200px;
    height: 960px;
    overflow: hidden;
    background: var(--backdrop);
    font-family: "Montserrat", sans-serif;
  }
  .letterhead {
    position: absolute;
    left: 252px;
    top: 30px;
    width: 696px;
    height: 900px;
    background: var(--paper);
    box-shadow: 0 6px 24px rgba(0,0,0,0.12);
    overflow: hidden;
  }
  .brand {
    position: absolute;
    left: 56px;
    top: 58px;
    display: flex;
    align-items: center;
    gap: 12px;
  }
  .brand-dot {
    width: 22px;
    height: 22px;
    border-radius: 50%;
    background: var(--copper);
  }
  .brand-name {
    font-weight: 700;
    font-size: 21px;
    letter-spacing: 0.5px;
    color: var(--navy);
    text-transform: uppercase;
  }
  .backdrop-mark {
    position: absolute;
    left: 188px;
    top: 290px;
    width: 320px;
    height: 320px;
    border-radius: 50%;
    border: 22px solid var(--faint);
    box-sizing: border-box;
  }
  .contact {
    position: absolute;
    right: 48px;
    bottom: 46px;
    color: var(--ink);
    font-size: 11.5px;
    letter-spacing: 0.4px;
    text-transform: uppercase;
  }
  .contact-license {
    display: flex;
    align-items: center;
    gap: 8px;
    padding-left: 42px;
    padding-bottom: 8px;
  }
  .contact-rule {
    height: 1.5px;
    background: var(--copper);
    width: 250px;
    margin-left: 30px;
  }
  .contact-lines {
    display: flex;
    gap: 26px;
    padding-top: 9px;
  }
  .edge-band {
    position: absolute;
    left: 0;
    right: 0;
    bottom: 0;
    height: 7px;
    background: var(--copper);
  }
</style>
</head>
<body>
  <main class="letterhead">
    <header class="brand">
      <span class="brand-dot"></span>
      <span class="brand-name">Copper Ridge Inquiries</span>
    </header>

    <div class="backdrop-mark" aria-hidden="true"></div>

    <footer class="contact">
      <div class="contact-license">
        <svg width="10" height="13" viewBox="0 0 10 13" aria-hidden="true">
          <path d="M5 0.5a4.3 4.3 0 0 0-4.3 4.3C0.7 8 5 12.5 5 12.5s4.3-4.5 4.3-7.7A4.3 4.3 0 0 0 5 0.5z" fill="var(--copper)"/>
          <circle cx="5" cy="4.8" r="1.6" fill="#fff"/>
        </svg>
        <span>Company License A41902735</span>
      </div>
      <div class="contact-rule"></div>
      <div class="contact-lines">
        <span>210.555.0148</span>
        <span>nora@copperridgeinquiries.com</span>
      </div>
    </footer>

    <div class="edge-band"></div>
  </main>
</body>
</html>
```